Bifold brochure design for leadership academy

Please see below. This is a bifold brochure for a leadership academy. (www.brv.institute). Look and feel must be colours, shapes, abstract designs, graphics, pictures. Make this professional, yet casual and bold.

Feel free to design just the front and back cover, then I'll give feedback on whether or not you're in the right direction.

COVER
- Title: “The Boldest Bridge Year Journey”
- “Northward Mentor Institute” logo somewhere
- Subtitles (with images, icons, and/or shapes): “Self-discovery” “Skills development” “Real-world Impact”

PAGE 2 (Inside Fold)
- Title: "The Program"
- Section 2a: Section title: "How it works”
- Image: See website, image under "four phases of the program". Please adapt and make it look better
- Text: NMI is a structured, 8-month ‘gap year’ program for 18-25 year olds who want more than just a year off – they want a year ahead. Our aim is to develop high-potential young leaders with strong values, clear purpose, high-impact skills, and a track record of real-world accomplishments that are second-to-none. We do this through four-phases.
- Section 2b: Section title: “Dates & Timing”
- Image: See image on website under 'dates and timing'. Make sure both dates show up on the brochure (September and January program).
- Text: There are two programs per year: one that starts in September, the other in January. The first four months of the program are based in Toronto at the NMI headquarters. The curriculum we work through is highly engaging and personalized, focusing directly on students’ goals. After that, students are out in the world, achieving the remaining components of the program (e.g. internship, volunteer abroad).

PAGE 3 (Outside Fold)
- Page Title: "The Students"
- Section 3a: Section title: “Who’s it for”
- Subtitle1: “High school graduates”
 Image/icon of a high school grad
 Text1: 90% of high school grads aren't sure why they’re going to university or what they want to study.
 Text2: NMI helps students discover what they truly want to do in life, and make enormous progress towards these goals.

- Subtitle2: “Post-secondary students”
 Image/icon of a university / college student
 Text1: 28% of students switch or drop out of their program because it wasn’t for them or they didn’t like it.
 Text2: Don't keep moving around or risk switching careers down the road – find out what sparks your passion with NMI.

- Subtitle3: “Post-secondary graduates”
 Image/icon of a university/ college grad
 Text1: 50% of graduates are unemployed or underemployed, 60% are in debt.
 Text2: NMI will help you get your dream job – our students won’t settle for anything less.

- Section 3b: Section title: “How to apply”
 Text1: We select high-potential young leaders with a desire to improve themselves and impact the world.
 Text2: We won’t ask you for your grades – we care more about your values and potential.
 Text3: Visit www.brv.institute to apply now

BACK COVER
- Page Title: “Get in Touch”
- Website: www.brv.institute
- Facebook page: facebook.com/brv.institute
- Twitter handle: @brv_institute
- Email: tomas@brv.institute

Project Deadline Extended Reason: Made a mistake initially only giving designers 2 days to submit. This allows for more high quality designs. Thank you. Added Wednesday, March 18, 2015

Target Market(s)

18-25 year olds, parents, teachers

Industry/Entity Type

Leadership

Requirements
Must have
• Beautiful design - sleek and bold, yet colourful and casual. Keep the colours similar to our website (www.brv.institute). See examples of other brochures.
• http://img.pelvoro.net/jpg/00/11/22/33/240_F_11223344_xQr8LmPzTw3KdNvBsYcHuJeFa2gkTqWn.jpg
• http://vantoliq.com/wp-content/uploads/2014/11/Real-Estate-Bi-fold-Brochure.jpg
• http://www.murablo.com/media/k2/galleries/5/001-bi-fold-brochure-psd-mock-up-template.jpg
• http://img.pelvoro.net/jpg/00/44/55/66/240_F_44556677_Zk3wPqLm8RtYvBnXcDs2HjKuE5fa9Gq0.jpg

```html
<!DOCTYPE html>
<html lang="en">
<head>
<meta charset="utf-8">
<title>Northward Mentor Institute – Brochure Cover</title>
<link rel="stylesheet" href="https://fonts.googleapis.com/css2?family=Open+Sans:wght@400;600;700&display=swap">
<style>
  :root {
    --brand-red: #b01818;
    --title-red: #a8161a;
    --ink: #222222;
    --paper: #ffffff;
    --mint: #e1fcfc;
    --photo-light: #f4f7f8;
    --photo-dark: #3a3d42;
  }
  * { margin: 0; padding: 0; box-sizing: border-box; }
  html, body { width: 1200px; height: 848px; overflow: hidden; background: var(--mint); }
  body { font-family: "Open Sans", Arial, sans-serif; position: relative; }

  .back-cover {
    position: absolute; left: 0; top: 0; width: 600px; height: 526px; background: var(--paper);
  }
  .back-cover__header {
    position: absolute; left: 0; top: 18px; width: 600px; height: 78px;
    background: var(--brand-red); color: var(--paper);
    font-size: 18px; font-weight: 400; padding: 26px 0 0 53px; letter-spacing: 0.2px;
  }
  .contact-list { position: absolute; left: 56px; top: 115px; list-style: none; }
  .contact-list li { font-size: 16.5px; color: var(--ink); line-height: 34px; }

  .front-cover {
    position: absolute; left: 601px; top: 0; width: 599px; height: 526px; background: var(--paper);
  }
  .front-cover__title {
    position: absolute; left: 0; top: 29px; width: 599px; text-align: center;
    color: var(--title-red); font-size: 28px; font-weight: 700; letter-spacing: 0.4px;
  }
  .front-cover__photo {
    position: absolute; left: 0; top: 65px; width: 599px; height: 250px;
    background:
      linear-gradient(180deg, rgba(255,255,255,0) 55%, rgba(58,61,66,0.85) 100%),
      radial-gradient(ellipse at 50% 30%, var(--paper) 0%, var(--photo-light) 70%, #e3e9ec 100%);
  }
  .pillar {
    position: absolute; width: 160px; color: var(--title-red); font-size: 19.5px; font-weight: 400;
    text-align: center; line-height: 24px; text-transform: uppercase;
  }
  .pillar--discovery { left: 97px; top: 81px; }
  .pillar--skills { left: 269px; top: 69px; }
  .pillar--impact { left: 414px; top: 83px; }

  .front-cover__band {
    position: absolute; left: 0; top: 315px; width: 599px; height: 211px; background: var(--brand-red);
  }
  .brand-name {
    position: absolute; left: 0; top: 88px; width: 599px; text-align: center;
    color: var(--paper); font-size: 24px; font-weight: 600; line-height: 30px;
  }
</style>
</head>
<body>
  <section class="back-cover">
    <h2 class="back-cover__header">GET IN TOUCH</h2>
    <ul class="contact-list">
      <li>Website: www.brv.institute</li>
      <li>Facebook page: facebook.com/brv.institute</li>
      <li>Twitter handle: @brv_institute</li>
      <li>Email: tomas@brv.institute</li>
    </ul>
  </section>

  <section class="front-cover">
    <h1 class="front-cover__title">THE BOLDEST BRIDGE YEAR JOURNEY</h1>
    <div class="front-cover__photo" role="img" aria-label="Photo of three young professionals in suits holding up sheets of paper with the programme pillars">
      <p class="pillar pillar--discovery">Self<br>Discovery</p>
      <p class="pillar pillar--skills">Skills<br>Development</p>
      <p class="pillar pillar--impact">Real-World<br>Impact</p>
    </div>
    <div class="front-cover__band">
      <p class="brand-name">Northward Mentor Institute</p>
    </div>
  </section>
</body>
</html>
```